Business Card for beauty technology startup

Design Glimora Business Card for a Beauty, based on the website identity and colors (https://www.glimora-example.com).
Glimora is a beauty tech startup that gathers helpful product info for beauty lovers and consumers (such as availability on stores, price range and product reviews) for makeup products. The card design must be young, colorful but clean, and very modern.

Target Market(s)

woman, 15-35

Industry/Entity Type

Cosmetics

Contact Information for Business Card

Full Name, address, phone

Font styles to use
Other font styles liked:
• Advent Pro

Colors
e34297
86cfc6
ffffff
5c5c5c
e8e8e8
e667a6
b2b2b2

Requirements
Must have
• One full colored side with a creative design and another with card info
• Use Color palette: #95C5C5 and/or #D38AA5
• Use fonts: Advent Pro
• Use website identity: https://www.glimora-example.com
Nice to have
• If needed extra font: Roboto

```html
<!DOCTYPE html>
<html lang="en">
<head>
<meta charset="utf-8">
<title>Glimora Business Card</title>
<link rel="stylesheet" href="https://fonts.googleapis.com/css2?family=Open+Sans:wght@300;400;600&display=swap">
<style>
  :root {
    --page-bg: #dcd9d7;
    --plum-light: #b06d8c;
    --plum-mid: #94506f;
    --plum-dark: #6f3350;
    --frost-light: #efeeee;
    --frost-mid: #dfdcdd;
    --frost-edge: #cfcacc;
    --text-soft: #f3e4eb;
    --text-bright: #ffffff;
    --brand-ink: #6a3049;
    --curve-line: #f6eef2;
  }
  * { margin: 0; padding: 0; box-sizing: border-box; }
  html, body {
    width: 1200px; height: 969px; overflow: hidden;
    background: var(--page-bg);
    font-family: "Open Sans", Arial, sans-serif;
  }
  .card {
    position: absolute; left: 100px; top: 200px;
    width: 1000px; height: 569px;
    overflow: hidden;
    background: linear-gradient(160deg, var(--frost-light), var(--frost-mid) 60%, var(--frost-edge));
    box-shadow: 0 18px 40px rgba(60, 40, 50, 0.25);
  }
  .card__shape { position: absolute; inset: 0; width: 1000px; height: 569px; }
  .contact {
    position: absolute; left: 48px; top: 100px;
    color: var(--text-soft);
  }
  .contact__name { font-size: 24px; font-weight: 600; color: var(--text-bright); letter-spacing: 0.3px; line-height: 34px; }
  .contact__role { font-size: 24px; font-weight: 400; line-height: 34px; }
  .contact__address { margin-top: 62px; font-size: 23px; line-height: 34px; }
  .contact__list { list-style: none; margin-top: 18px; }
  .contact__item {
    display: flex; align-items: center; gap: 14px;
    font-size: 22px; line-height: 32px;
  }
  .contact__icon { width: 20px; height: 20px; flex: none; fill: var(--text-soft); }
  .brand__mark {
    position: absolute; left: 634px; top: 147px;
    width: 162px; height: 162px;
    border: 3px solid var(--brand-ink);
    border-radius: 50%;
  }
  .brand {
    position: absolute; left: 520px; width: 410px; top: 366px;
    text-align: center;
    font-size: 66px; font-weight: 300; letter-spacing: 9px;
    color: var(--brand-ink);
  }
</style>
</head>
<body>
  <main class="card">
    <svg class="card__shape" viewBox="0 0 1000 569" aria-hidden="true">
      <defs>
        <linearGradient id="plumPanel" x1="0" y1="0" x2="1" y2="1">
          <stop offset="0" stop-color="var(--plum-light)"/>
          <stop offset="0.55" stop-color="var(--plum-mid)"/>
          <stop offset="1" stop-color="var(--plum-dark)"/>
        </linearGradient>
      </defs>
      <path d="M0 0 H560 Q236 284 552 569 H0 Z" fill="url(#plumPanel)"/>
      <path d="M560 0 Q236 284 552 569" fill="none" stroke="var(--curve-line)" stroke-width="3" stroke-opacity="0.8"/>
    </svg>

    <section class="contact">
      <p class="contact__name">CLARA VENN</p>
      <p class="contact__role">CEO/FOUNDER</p>
      <p class="contact__address">1204 Lilac Row<br>Fairview, Oregon 55012</p>
      <ul class="contact__list">
        <li class="contact__item">
          <svg class="contact__icon" viewBox="0 0 20 20"><path d="M3 7c0-3 3-4 7-4s7 1 7 4v1h-4V6H7v2H3z"/><rect x="4" y="10" width="12" height="7" rx="1.5"/></svg>
          555 214 0381
        </li>
        <li class="contact__item">
          <svg class="contact__icon" viewBox="0 0 20 20"><path d="M6 1h8a1 1 0 0 1 1 1v16a1 1 0 0 1-1 1H6a1 1 0 0 1-1-1V2a1 1 0 0 1 1-1zm1 3v10h6V4z"/></svg>
          555 730 1926
        </li>
        <li class="contact__item">
          <svg class="contact__icon" viewBox="0 0 20 20"><rect x="5" y="2" width="10" height="6"/><path d="M2 9h16v7h-3v2H5v-2H2zm5 4v3h6v-3z"/></svg>
          555 468 2053
        </li>
        <li class="contact__item">
          <svg class="contact__icon" viewBox="0 0 20 20"><path d="M2 5h16v10H2zm1.5 1.2L10 11l6.5-4.8V5.8H3.5z"/></svg>
          info@glimora-example.com
        </li>
        <li class="contact__item">
          <svg class="contact__icon" viewBox="0 0 20 20"><path d="M10 2a8 8 0 1 0 0 16 8 8 0 0 0 0-16zm-1 2.2v3l-3 1-1.6-1.8A6 6 0 0 1 9 4.2zm2.5 11.5-1-3 2.5-2.2 2.6 1A6 6 0 0 1 11.5 15.7z"/></svg>
          www.glimora-example.com
        </li>
      </ul>
    </section>

    <div class="brand__mark" aria-hidden="true"></div>
    <p class="brand">GLIMORA</p>
  </main>
</body>
</html>
```